Carpet cleaning company focused on high quality needs business cards

We are a growing company that just merged with another company and need to design a new business card. We do both residential as well as commercial cleaning. We do carpet, tile & grout, upholstery, hard floors, and stain & pet odor removal. We treat our customers like family and strive to achieve outstanding results with every job.

```html
<!DOCTYPE html>
<html lang="en">
<head>
<meta charset="utf-8">
<title>Vapor Crew Cleaning – Business Card</title>
<link rel="stylesheet" href="https://fonts.googleapis.com/css2?family=Montserrat:wght@400;500;700;800&display=swap">
<style>
  :root {
    --brand-red: #e9493f;
    --ink: #2b2d33;
    --paper: #ffffff;
    --backdrop: #2a2b30;
    --mascot-blue: #2f7fc1;
    --mascot-tan: #b89158;
  }
  * { box-sizing: border-box; margin: 0; padding: 0; }
  html, body {
    width: 1200px; height: 900px; overflow: hidden;
    background: var(--backdrop);
    font-family: "Montserrat", sans-serif;
  }
  .stage {
    position: relative; width: 1200px; height: 900px;
  }
  .card {
    position: absolute; left: 250px;
    width: 700px; height: 400px;
    border-radius: 24px; overflow: hidden;
  }
  .card--front { top: 30px; background: var(--brand-red); }
  .card--back  { top: 470px; background: var(--paper); }

  /* front */
  .front-mascot {
    position: absolute; left: 130px; top: 110px;
    width: 180px; height: 180px; border-radius: 12px;
    background: linear-gradient(135deg, var(--mascot-blue) 0%, #5c6b7a 55%, var(--mascot-tan) 100%);
    opacity: .85;
  }
  .wordmark {
    color: var(--ink); font-weight: 800; text-transform: uppercase;
    line-height: 1.02; letter-spacing: -.5px;
  }
  .front-wordmark {
    position: absolute; left: 350px; top: 140px;
    font-size: 44px;
  }

  /* back */
  .back-accent {
    position: absolute; right: 0; top: 0; width: 320px; height: 300px;
  }
  .back-mascot {
    position: absolute; right: 20px; top: 20px;
    width: 250px; height: 210px; border-radius: 14px;
    background: linear-gradient(150deg, #e8eef3 0%, var(--mascot-blue) 50%, var(--mascot-tan) 100%);
  }
  .back-wordmark {
    position: absolute; left: 44px; top: 118px;
    font-size: 30px;
  }
  .contact {
    position: absolute; left: 44px; top: 210px;
    color: var(--ink);
  }
  .contact__name {
    color: var(--brand-red); font-weight: 700; font-size: 28px; line-height: 1.1;
  }
  .contact__title { font-size: 14px; font-weight: 500; margin-top: 2px; }
  .contact__address { font-size: 13px; line-height: 1.4; margin-top: 10px; }
  .contact__list { list-style: none; margin-top: 10px; font-size: 13px; }
  .contact__list li { display: flex; align-items: center; gap: 10px; line-height: 1.6; }
  .contact__list svg { width: 14px; height: 14px; fill: var(--brand-red); flex: none; }
</style>
</head>
<body>
<main class="stage">

  <section class="card card--front" aria-label="Card front">
    <div class="front-mascot" role="img" aria-label="Cartoon cleaning technician in a blue cap and shirt holding a steam wand and hose"></div>
    <div class="wordmark front-wordmark">Vapor Crew<br>Cleaning</div>
  </section>

  <section class="card card--back" aria-label="Card back">
    <svg class="back-accent" viewBox="0 0 320 300" aria-hidden="true">
      <polygon points="60,250 150,160 320,160 320,300 60,300" fill="var(--brand-red)"/>
    </svg>
    <div class="back-mascot" role="img" aria-label="Cartoon cleaning technician lifting a steam wand, spray fanning out below"></div>

    <div class="wordmark back-wordmark">Vapor Crew<br>Cleaning</div>

    <div class="contact">
      <p class="contact__name">Daniel Harper</p>
      <p class="contact__title">CEO</p>
      <p class="contact__address">418 Maple Grove Ave, #112<br>Riverton, OH 43190</p>
      <ul class="contact__list">
        <li>
          <svg viewBox="0 0 24 24"><path d="M6.6 10.8a15 15 0 0 0 6.6 6.6l2.2-2.2c.3-.3.7-.4 1-.2 1.1.4 2.3.6 3.6.6.6 0 1 .4 1 1V20c0 .6-.4 1-1 1C10.6 21 3 13.4 3 4c0-.6.4-1 1-1h3.5c.6 0 1 .4 1 1 0 1.3.2 2.5.6 3.6.1.3 0 .7-.2 1z"/></svg>
          555 318-2704
        </li>
        <li>
          <svg viewBox="0 0 24 24"><path d="M7 1h10a2 2 0 0 1 2 2v18a2 2 0 0 1-2 2H7a2 2 0 0 1-2-2V3a2 2 0 0 1 2-2zm0 3v14h10V4zm5 15.5a1 1 0 1 0 0 2 1 1 0 0 0 0-2z"/></svg>
          555 318-2704
        </li>
        <li>
          <svg viewBox="0 0 24 24"><path d="M2 5h20v14H2zm2 2v.5l8 5 8-5V7l-8 5z"/></svg>
          hello@vaporcrewclean.com
        </li>
        <li>
          <svg viewBox="0 0 24 24"><path d="M12 2a10 10 0 1 0 0 20 10 10 0 0 0 0-20zm6.9 6h-3a15 15 0 0 0-1.3-4A8 8 0 0 1 18.9 8zM12 4c.8 1.2 1.5 2.5 1.9 4h-3.8c.4-1.5 1.1-2.8 1.9-4zM4.3 14a8 8 0 0 1 0-4h3.4a16 16 0 0 0 0 4zm.8 2h3a15 15 0 0 0 1.3 4A8 8 0 0 1 5.1 16zm3-8h-3a8 8 0 0 1 4.3-4 15 15 0 0 0-1.3 4zM12 20c-.8-1.2-1.5-2.5-1.9-4h3.8c-.4 1.5-1.1 2.8-1.9 4zm2.3-6H9.7a14 14 0 0 1 0-4h4.6a14 14 0 0 1 0 4zm.3 6a15 15 0 0 0 1.3-4h3a8 8 0 0 1-4.3 4zm1.7-6a16 16 0 0 0 0-4h3.4a8 8 0 0 1 0 4z"/></svg>
          www.vaporcrewclean.com
        </li>
      </ul>
    </div>
  </section>

</main>
</body>
</html>
```